Tolbek cards

I want a simple business card that pops.
Logo on one side.
On side two i want.
"Are you thinking about a new building on your property, or renovating an existing structure? Contact".....
Owners Name: Dale Whitacre
Owners Phone number: 610-555-0187
Address:4076 Copper Ridge RD, Bedford, PA 15522
Committed to Quality, Service, and Integrity

```html
<!DOCTYPE html>
<html lang="en">
<head>
<meta charset="utf-8">
<title>Tolbek Builders LLC – Business Card</title>
<link rel="stylesheet" href="https://fonts.googleapis.com/css2?family=Roboto:wght@500;700;900&family=Poppins:wght@400&display=swap">
<style>
  :root {
    --backdrop: #f0f0f0;
    --card: #ffffff;
    --brown: #3f2d1c;
    --ink: #111111;
    --shadow: rgba(0, 0, 0, 0.28);
  }
  * { box-sizing: border-box; margin: 0; padding: 0; }
  html, body {
    width: 1200px;
    height: 990px;
    overflow: hidden;
    background: var(--backdrop);
  }
  .sheet {
    position: relative;
    width: 1200px;
    height: 990px;
  }
  .card {
    position: absolute;
    left: 244px;
    width: 712px;
    height: 407px;
    background: var(--card);
    border-radius: 36px;
    box-shadow: 0 10px 28px var(--shadow);
    text-align: center;
    font-family: "Roboto", sans-serif;
  }
  .card--front { top: 68px; }
  .card--back { top: 516px; }

  .brand {
    position: absolute;
    left: 0; right: 0;
    top: 74px;
    display: flex;
    flex-direction: column;
    align-items: center;
    color: var(--brown);
    font-weight: 900;
  }
  .brand__mark {
    width: 62px;
    height: 62px;
    background: var(--brown);
    margin-bottom: 26px;
  }
  .brand__name {
    font-size: 86px;
    line-height: 0.9;
    letter-spacing: 1px;
  }
  .brand__sub {
    font-size: 28px;
    letter-spacing: 2px;
    margin-top: 10px;
  }

  .line {
    position: absolute;
    left: 0; right: 0;
  }
  .tagline {
    top: 24px;
    font-size: 16.5px;
    font-weight: 500;
    color: var(--ink);
    letter-spacing: 0.3px;
  }
  .owner-name {
    top: 160px;
    font-size: 37px;
    font-weight: 700;
    color: var(--brown);
    letter-spacing: 0.3px;
  }
  .owner-role {
    top: 196px;
    font-family: "Poppins", sans-serif;
    font-size: 17px;
    color: var(--ink);
    letter-spacing: 0.5px;
  }
  .divider {
    top: 226px;
    display: flex;
    justify-content: center;
  }
  .contact {
    font-size: 17px;
    font-weight: 500;
    color: var(--ink);
    letter-spacing: 0.8px;
  }
  .contact--phone { top: 255px; }
  .contact--address { top: 278px; }
  .pitch {
    top: 338px;
    padding: 0 50px;
    font-size: 17px;
    font-weight: 500;
    line-height: 23px;
    color: var(--ink);
    letter-spacing: 0.3px;
  }
</style>
</head>
<body>
<main class="sheet">
  <section class="card card--front" aria-label="Card front">
    <div class="brand">
      <span class="brand__mark" aria-hidden="true"></span>
      <span class="brand__name">TOLBEK</span>
      <span class="brand__sub">BUILDERS LLC</span>
    </div>
  </section>

  <section class="card card--back" aria-label="Card back">
    <p class="line tagline">Committed to Quality, Service, and Integrity</p>
    <h1 class="line owner-name">Dale Whitacre</h1>
    <p class="line owner-role">Owners</p>
    <div class="line divider" aria-hidden="true">
      <svg width="216" height="20" viewBox="0 0 216 20">
        <g fill="var(--brown)">
          <circle cx="2" cy="10" r="1.8"/>
          <circle cx="14" cy="10" r="2.2"/>
          <circle cx="26" cy="10" r="2.6"/>
          <circle cx="38" cy="10" r="3.1"/>
          <circle cx="50" cy="10" r="3.6"/>
          <circle cx="61" cy="10" r="4.1"/>
          <circle cx="73" cy="10" r="4.6"/>
          <circle cx="143" cy="10" r="4.6"/>
          <circle cx="155" cy="10" r="4.1"/>
          <circle cx="166" cy="10" r="3.6"/>
          <circle cx="178" cy="10" r="3.1"/>
          <circle cx="190" cy="10" r="2.6"/>
          <circle cx="202" cy="10" r="2.2"/>
          <circle cx="214" cy="10" r="1.8"/>
          <circle cx="92" cy="10" r="9"/>
          <circle cx="123" cy="10" r="9"/>
        </g>
        <path d="M88 6.2c.6-.6 1.3-.5 1.7.1l.8 1.3c.3.5.2 1-.2 1.3l-.5.4c.4 1 1.2 1.9 2.2 2.4l.4-.5c.3-.4.9-.5 1.3-.2l1.3.8c.6.4.7 1.1.1 1.7-1 1-2.5 1-4.1-.3-1.4-1.1-2.6-2.6-3.2-4.1-.5-1.3-.4-2.3.2-2.9z" fill="#fff"/>
        <path d="M123 4.5a3.6 3.6 0 0 0-3.6 3.6c0 2.6 3.6 6.4 3.6 6.4s3.6-3.8 3.6-6.4A3.6 3.6 0 0 0 123 4.5zm0 5a1.4 1.4 0 1 1 0-2.8 1.4 1.4 0 0 1 0 2.8z" fill="#fff"/>
      </svg>
    </div>
    <p class="line contact contact--phone">610-555-0187</p>
    <p class="line contact contact--address">4076 Copper Ridge RD, Bedford, PA 15522</p>
    <p class="line pitch">"Are you thinking about a new building on your property, or renovating an existing structure? Contact".....</p>
  </section>
</main>
</body>
</html>
```